Occupational Medical Billing and Coding Business needs Postcard

Medical billing and coding business needs marketing postcard to send to target audience of orthopaedic surgeons who practice medicine in California Workers' Compensation industry. These doctors treat injured workers and/or provide medical-legal evaluations and reports for the courts to settle the injured worker's claim. This is a highly specialized area of medical billing and coding. It is extremely complicated and can be very frustrating for doctors and their staff who do not understand the system. I would encourage the designers to check out my website: www.MarlowBrookMedicalBilling.com
I want something bright and colorful that makes bold statements. It has to get their attention. My suggestions for bold statements include:
1) QMEs! Are your bills compliant with DWC's view? We make sure your complexity factors are maximized as well as compliant.
2) We collected over $ 462,000 just in second bill review (SBR) appeals alone and that's just one orthopaedic surgeon! Imagine what we can do for you!

I uploaded a word document with some information about the services I offer. The company logo is also there. Let me know if you need it in another format. The items with the asterisk (**) must be in the postcard.

Thank you so much!

Marlow Brook Medical Billing

Target Market(s)

Orthopaedic Surgeons who treat injured workers in California

Font styles to use
Sans Serif

Colors

Designer to choose colors to be used in the design.

Requirements
Must have
• Expert Billing and Coding Services for:
• QME - AME - IME Evaluations
• Radiology - MRI/CT Scans
• Orthopaedic Surgery
• Certified Coders on Staff
• Electronic Claim Submission
• Payment within 15 days
• It's important to spell orthopaedic with the "A" after the "P" as it is an acknowledgment of the origins of the practice and will attract a doctor with higher education.

```html
<!DOCTYPE html>
<html lang="en">
<head>
<meta charset="utf-8">
<title>Marlow Brook Medical Billing – Postcard</title>
<link href="https://fonts.googleapis.com/css2?family=Montserrat:wght@400;500;600;700;800&display=swap" rel="stylesheet">
<style>
  :root{
    --teal:#2b7b80;
    --teal-dark:#23686c;
    --lime:#8dc63f;
    --white:#ffffff;
    --ink:#3b4a4c;
    --canvas:#ececec;
    --room-light:#eef1f0;
    --room-mid:#d9dedc;
    --line:#b9c2c2;
  }
  *{box-sizing:border-box;margin:0;padding:0}
  html,body{width:690px;height:1200px;overflow:hidden}
  body{background:var(--canvas);font-family:"Montserrat",sans-serif;position:relative}
  .card{position:absolute;left:35px;width:620px;height:413px;background:var(--white);overflow:hidden;box-shadow:0 4px 14px rgba(0,0,0,.18)}
  .card--front{top:150px}
  .card--back{top:630px}

  /* brand */
  .brand{position:absolute;display:flex;align-items:center;gap:7px;color:var(--teal);font-weight:600;font-size:13px;line-height:1.15}
  .brand__mark{width:9px;height:9px;background:var(--lime);flex:none}

  /* front */
  .headline{position:absolute;left:0;top:0;width:330px}
  .headline__main{padding:22px 0 0 22px;height:64px;color:var(--teal);font-weight:800;font-size:31px;letter-spacing:.3px;line-height:1;white-space:nowrap}
  .headline__sub{background:var(--lime);color:var(--white);font-weight:600;font-size:15px;letter-spacing:.4px;padding:7px 22px;height:30px;white-space:nowrap}
  .front .brand{left:396px;top:30px;width:200px}
  .services{position:absolute;left:0;top:94px;width:330px;height:236px;background:var(--teal);padding:14px 18px 0 22px;list-style:none}
  .services li{display:flex;align-items:flex-start;gap:10px;color:var(--white);margin-bottom:9px}
  .services .icon{flex:none;width:20px;height:20px}
  .services strong{display:block;font-size:12px;font-weight:700;line-height:1.2}
  .services small{display:block;font-size:8.5px;font-weight:400;opacity:.9;line-height:1.3}
  .services li.single{align-items:center}
  .photo{position:absolute;left:330px;top:78px;width:290px;height:252px;background:linear-gradient(180deg,var(--room-light) 0%,var(--room-mid) 70%,#c9cfcc 100%)}
  .experience{position:absolute;left:22px;top:350px;width:296px;color:var(--teal);line-height:1.15;white-space:nowrap}
  .experience span{display:block;font-size:17px;font-weight:800}
  .experience em{display:block;font-style:normal;font-size:13px;font-weight:500;letter-spacing:.2px}
  .contact-strip{position:absolute;left:330px;top:330px;width:290px;height:83px;background:var(--lime);color:var(--white);padding:22px 22px}
  .contact-strip .call{font-size:16px;font-weight:600;letter-spacing:.3px;white-space:nowrap}
  .contact-strip .web{font-size:9.5px;font-weight:500;margin-top:4px}

  /* back */
  .back__title{position:absolute;left:22px;top:28px;color:var(--teal);font-weight:700;font-size:12.5px;letter-spacing:.3px}
  .back .brand{left:405px;top:22px;width:200px}
  .collections{position:absolute;left:0;top:70px;width:335px;height:343px;background:var(--teal);color:var(--white);padding:22px 22px}
  .collections__text{font-size:9.5px;line-height:1.5;margin-bottom:12px;font-weight:500}
  .reach{position:absolute;left:22px;bottom:22px;width:291px;background:var(--lime);padding:12px 14px;color:var(--white)}
  .reach .call{font-size:16px;font-weight:600;margin-bottom:6px;white-space:nowrap}
  .reach .label{font-size:9px;font-weight:700;line-height:1.4}
  .reach .value{font-size:9px;font-weight:500;line-height:1.4;margin-bottom:4px}
  .stamp{position:absolute;right:22px;top:90px;width:58px;height:66px;border:1.5px solid var(--line)}
  .address-lines{position:absolute;left:405px;top:260px;width:190px}
  .address-lines span{display:block;border-bottom:1.5px solid var(--line);height:30px}
</style>
</head>
<body>

<section class="card card--front front" aria-label="Postcard front">
  <div class="headline">
    <h1 class="headline__main">EXPERT BILLING</h1>
    <p class="headline__sub">AND CODING SERVICES FOR</p>
  </div>
  <div class="brand"><span class="brand__mark"></span>Marlow Brook<br>Medical Billing</div>

  <ul class="services">
    <li><svg class="icon" viewBox="0 0 20 20"><circle cx="10" cy="10" r="10" fill="#fff"/><path d="M5.5 10.3l3 3 6-6.3" fill="none" stroke="#2b7b80" stroke-width="2"/></svg><div><strong>QME – AME – IME Evaluations</strong><small>Treatment – Primary/Secondary Physician</small></div></li>
    <li><svg class="icon" viewBox="0 0 20 20"><circle cx="10" cy="10" r="10" fill="#fff"/><path d="M5.5 10.3l3 3 6-6.3" fill="none" stroke="#2b7b80" stroke-width="2"/></svg><div><strong>Radiology – MRI/CT Scans</strong><small>Electrodiagnostic Studies</small></div></li>
    <li><svg class="icon" viewBox="0 0 20 20"><circle cx="10" cy="10" r="10" fill="#fff"/><path d="M5.5 10.3l3 3 6-6.3" fill="none" stroke="#2b7b80" stroke-width="2"/></svg><div><strong>Orthopaedic Surgery</strong><small>Arthroplasty, Spine, Hand Surgery</small></div></li>
    <li class="single"><svg class="icon" viewBox="0 0 20 20"><circle cx="10" cy="10" r="10" fill="#fff"/><path d="M5.5 10.3l3 3 6-6.3" fill="none" stroke="#2b7b80" stroke-width="2"/></svg><strong>Certified Coders on Staff</strong></li>
    <li class="single"><svg class="icon" viewBox="0 0 20 20"><circle cx="10" cy="10" r="10" fill="#fff"/><path d="M5.5 10.3l3 3 6-6.3" fill="none" stroke="#2b7b80" stroke-width="2"/></svg><strong>Electronic Claim Submission</strong></li>
    <li class="single"><svg class="icon" viewBox="0 0 20 20"><circle cx="10" cy="10" r="10" fill="#fff"/><path d="M5.5 10.3l3 3 6-6.3" fill="none" stroke="#2b7b80" stroke-width="2"/></svg><strong>Payment within 15 days</strong></li>
  </ul>

  <div class="photo" role="img" aria-label="Photo of a bright, modern office meeting room with white table and chairs"></div>

  <p class="experience"><span>OVER 25 YEARS EXPERIENCE</span><em>IN WORKERS' COMP</em></p>
  <div class="contact-strip">
    <p class="call">CALL TODAY: 714. 555.0142</p>
    <p class="web">www.MarlowBrookMedicalBilling.com</p>
  </div>
</section>

<section class="card card--back back" aria-label="Postcard back">
  <h2 class="back__title">WE ALSO PROVIDE COLLECTION SERVICES</h2>
  <div class="brand"><span class="brand__mark"></span>Marlow Brook<br>Medical Billing</div>

  <div class="collections">
    <p class="collections__text">Expert Denial Management, Timely filing of SBR and IBR Appeals. Collected over $462,000 just in second bill review appeals. This is an example of ONE orthopaedic surgeon to date. Imagine what we can do for you!</p>
    <p class="collections__text">We get your medical legal bills paid including penalty, interest and in some cases costs associated with the effort to collect.</p>
    <div class="reach">
      <p class="call">CALL TODAY: 714. 555.0142</p>
      <p class="label">Send us an Email:</p>
      <p class="value">info@MarlowBrookMedicalBilling.com</p>
      <p class="label">Visit our Website:</p>
      <p class="value">www.MarlowBrookMedicalBilling.com</p>
    </div>
  </div>

  <div class="stamp"></div>
  <div class="address-lines"><span></span><span></span><span></span><span></span></div>
</section>

</body>
</html>
```